bird wings, breathing, coaching, rhythm, heart

I would like this card design to be inspired by the following Rumi poem - now that I see some cards with the poem on it, I am pretty sure I don't want that. The feel of the cards should be watery and emotional, one of rhythm, breathing like a pendulum. An Ouroboros, (alchemical imagery in general), Birds, lungs, bird wings, hands, clouds, water, waves and rivers are all good images. Simple elegance is appreciated.
Cards should contain my name, title (coach), address, phone number and email address.
Your grief for what you've lost lifts a mirror
up to where you're bravely working.
Expecting the worst, you look, and instead,
here's the joyful face you've been wanting to see.
Your hand opens and closes and opens and closes.
If it were always a fist or always stretched open,
you would be paralyzed.
Your deepest presence
is in every small contracting and expanding,
the two as beautifully balanced and coordinated
as birdwings.
Contact Information for Business Card
Dorran Pelkwith, MA
Coach
4718 Varno St.
Berkeley, CA 94188
415-382-6649
pelkwith@mailvaro.net
Designer to choose colors to be used in the design.

```html
<!DOCTYPE html>
<html lang="en">
<head>
<meta charset="utf-8">
<title>Dorran Pelkwith, MA — Coach · Business Card</title>
<link rel="stylesheet" href="https://fonts.googleapis.com/css2?family=Lato:wght@400;700&family=Oswald:wght@500&display=swap">
<style>
  :root {
    --backdrop: #2b2b2d;
    --card-white: #ffffff;
    --navy: #0b1a28;
    --blue: #2179b9;
    --blue-light: #3592d6;
    --blue-mist: #cfe3f3;
    --contact-ink: #2f2f2f;
  }
  html, body {
    margin: 0;
    padding: 0;
    width: 1200px;
    height: 900px;
    overflow: hidden;
    background: var(--backdrop);
  }
  .stage {
    position: relative;
    width: 1200px;
    height: 900px;
  }
  .card {
    position: absolute;
    left: 300px;
    width: 600px;
    height: 343px;
    background: var(--card-white);
    overflow: hidden;
    box-shadow: 0 10px 24px rgba(0,0,0,0.45);
  }
  .card-back { top: 70px; }
  .card-front { top: 473px; }
  .card-shapes {
    position: absolute;
    inset: 0;
    width: 600px;
    height: 343px;
  }
  .breath-wave {
    fill: none;
    stroke-linecap: round;
  }
  .identity {
    position: absolute;
    left: 222px;
    top: 150px;
    color: var(--card-white);
  }
  .identity-name {
    margin: 0;
    font-family: "Oswald", sans-serif;
    font-weight: 500;
    font-size: 27px;
    letter-spacing: 0.2px;
    text-transform: uppercase;
    line-height: 1.1;
  }
  .identity-title {
    margin: 2px 0 0 -8px;
    font-family: "Lato", sans-serif;
    font-weight: 400;
    font-size: 19px;
    line-height: 1.1;
  }
  .contact-list {
    position: absolute;
    left: 196px;
    top: 252px;
    margin: 0;
    padding: 0;
    list-style: none;
    font-family: "Lato", sans-serif;
    font-weight: 400;
    font-size: 20px;
    color: var(--contact-ink);
  }
  .contact-item {
    display: flex;
    align-items: center;
    gap: 6px;
    height: 27px;
  }
  .contact-icon {
    width: 16px;
    height: 16px;
    fill: var(--blue);
    flex: none;
  }
</style>
</head>
<body>
<main class="stage">

  <section class="card card-back" aria-label="Card back">
    <svg class="card-shapes" viewBox="0 0 600 343" aria-hidden="true">
      <polygon points="0,0 600,0 600,34 0,16" fill="var(--navy)"/>
      <polygon points="470,27 600,34 600,140" fill="var(--blue)"/>
      <polygon points="470,27 515,29 540,62" fill="var(--blue-light)"/>
      <polygon points="0,302 600,322 600,343 0,343" fill="var(--navy)"/>
      <polygon points="0,160 0,302 92,305" fill="var(--blue)"/>
      <polygon points="62,304 92,305 72,290" fill="var(--blue-light)"/>
      <path class="breath-wave" d="M120,150 C190,95 250,95 300,150 S410,205 480,150" stroke="var(--blue)" stroke-width="4"/>
      <path class="breath-wave" d="M140,180 C205,130 255,130 300,180 S395,230 460,180" stroke="var(--blue-light)" stroke-width="3"/>
      <path class="breath-wave" d="M160,210 C215,170 260,170 300,210 S380,250 440,210" stroke="var(--blue-mist)" stroke-width="2.5"/>
    </svg>
  </section>

  <section class="card card-front" aria-label="Card front with contact details">
    <svg class="card-shapes" viewBox="0 0 600 343" aria-hidden="true">
      <rect x="0" y="138" width="600" height="100" fill="var(--navy)"/>
      <polygon points="0,0 340,0 0,343" fill="var(--blue)"/>
      <polygon points="262,78 340,0 352,138 201,138" fill="var(--blue-light)"/>
      <polygon points="262,78 340,0 201,138" fill="var(--blue)"/>
      <path class="breath-wave" d="M360,300 C400,282 430,282 465,300 S530,318 580,300" stroke="var(--blue-mist)" stroke-width="2.5"/>
    </svg>

    <div class="identity">
      <h1 class="identity-name">Dorran Pelkwith, MA</h1>
      <p class="identity-title">Coach</p>
    </div>

    <ul class="contact-list">
      <li class="contact-item">
        <svg class="contact-icon" viewBox="0 0 16 16" aria-hidden="true">
          <path d="M1 5c0-2 3-3 7-3s7 1 7 3v1.5h-3.5V5h-7v1.5H1z M3 8l2-2h6l2 2v6H3z"/>
          <circle cx="8" cy="10.5" r="1.8" fill="#fff"/>
        </svg>
        <span>415-382-6649</span>
      </li>
      <li class="contact-item">
        <svg class="contact-icon" viewBox="0 0 16 16" aria-hidden="true">
          <rect x="1" y="3" width="14" height="10" rx="1"/>
          <path d="M1.5 3.8 8 9l6.5-5.2" fill="none" stroke="#fff" stroke-width="1.3"/>
        </svg>
        <span>pelkwith@mailvaro.net</span>
      </li>
      <li class="contact-item">
        <svg class="contact-icon" viewBox="0 0 16 16" aria-hidden="true">
          <path d="M8 0.5a5 5 0 0 0-5 5c0 3.8 5 10 5 10s5-6.2 5-10a5 5 0 0 0-5-5z"/>
          <circle cx="8" cy="5.5" r="2" fill="#fff"/>
        </svg>
        <span>4718 Varno St. Berkeley, CA 94188</span>
      </li>
    </ul>
  </section>

</main>
</body>
</html>
```